A ebook cover to reinvent the imagery of vegetable companion gardening

We needs a ebook design with illustrates minimal as well as clear and concise relevance to vegetable companion gardening . we will add a mock up design and other existing designs to help you gauge and create the sort of illustration fit for our aims.
Book Title: Orchard and Greens 202 – Garden Partner Sowing
Subtitle: Partner Handbook On Raising Crops Through Basic, Natural & Lasting Plot Methods
(Perfect For Beginners)
Author: Amber Hollow
Size: 5.5 x 8.5

```html
<!DOCTYPE html>
<html lang="en">
<head>
<meta charset="utf-8">
<title>Orchard and Greens 202 – Garden Partner Sowing</title>
<link rel="stylesheet" href="https://fonts.googleapis.com/css2?family=Bebas+Neue&family=Montserrat:wght@400;700&family=Poppins:wght@700&display=swap">
<style>
  :root {
    --page-bg: #c4c4c4;
    --cover-white: #ffffff;
    --plank-grey: #eceef0;
    --title-black: #111111;
    --title-orange: #ff6a00;
    --band-green: #3b9a1d;
    --author-green: #3aa01e;
    --leaf-dark: #4f8f2c;
    --leaf-light: #9fcf5a;
    --tomato-red: #d8321f;
    --tomato-light: #f06a4a;
    --cabbage-purple: #8a2a6a;
    --basket-brown: #a8652a;
    --pepper-yellow: #e8b21e;
    --fruit-orange: #f08a2a;
    --grape-green: #b7c95a;
    --text-white: #ffffff;
  }
  html, body {
    margin: 0;
    padding: 0;
    width: 1200px;
    height: 2538px;
    overflow: hidden;
    background: var(--page-bg);
  }
  .cover {
    position: absolute;
    left: 50px;
    top: 419px;
    width: 1100px;
    height: 1700px;
    overflow: hidden;
    background: linear-gradient(90deg, var(--plank-grey) 0%, var(--cover-white) 20%, var(--cover-white) 80%, var(--plank-grey) 100%);
    box-shadow: 0 30px 50px rgba(0,0,0,0.28);
  }
  .produce { position: absolute; }
  .produce-top-left {
    left: 0; top: 0;
    width: 410px; height: 400px;
    border-bottom-right-radius: 100% 100%;
    background: linear-gradient(150deg, var(--leaf-dark) 0%, var(--leaf-light) 100%);
  }
  .produce-top-centre {
    left: 520px; top: 0;
    width: 200px; height: 215px;
    border-radius: 0 0 100px 100px;
    background: linear-gradient(180deg, var(--tomato-red) 0%, var(--tomato-light) 100%);
  }
  .produce-top-right {
    left: 700px; top: 0;
    width: 400px; height: 420px;
    border-bottom-left-radius: 100% 100%;
    background: linear-gradient(200deg, var(--leaf-light) 0%, var(--leaf-dark) 70%, var(--cabbage-purple) 100%);
  }
  .produce-basket {
    left: 660px; top: 890px;
    width: 440px; height: 810px;
    border-top-left-radius: 220px 260px;
    background: linear-gradient(160deg, var(--basket-brown) 0%, var(--pepper-yellow) 35%, var(--cabbage-purple) 60%, var(--tomato-red) 100%);
  }
  .produce-fruit {
    left: 40px; top: 1240px;
    width: 660px; height: 460px;
    border-top-left-radius: 330px 220px;
    border-top-right-radius: 200px 160px;
    background: linear-gradient(90deg, var(--grape-green) 0%, var(--fruit-orange) 40%, var(--tomato-light) 65%, var(--leaf-light) 100%);
  }
  .title {
    position: absolute;
    left: 0; top: 325px;
    width: 1100px;
    margin: 0;
    text-align: center;
    font-family: "Bebas Neue", "Oswald", sans-serif;
    font-weight: 400;
    line-height: 0.86;
  }
  .title-top {
    display: flex;
    justify-content: center;
    align-items: flex-end;
    gap: 8px;
    font-size: 200px;
    color: var(--title-black);
  }
  .title-rule {
    display: block;
    width: 60px;
    height: 9px;
    background: var(--title-black);
    margin-bottom: 26px;
  }
  .title-main {
    display: block;
    font-size: 242px;
    color: var(--title-orange);
    margin-top: 14px;
  }
  .series-band {
    position: absolute;
    left: 74px; top: 738px;
    width: 947px; height: 84px;
    border-radius: 6px;
    background: var(--band-green);
    color: var(--text-white);
    font-family: "Poppins", sans-serif;
    font-weight: 700;
    font-size: 56px;
    line-height: 88px;
    text-align: center;
    letter-spacing: 0.5px;
  }
  .subtitle {
    position: absolute;
    left: 82px; top: 860px;
    width: 460px;
    margin: 0;
    font-family: "Montserrat", sans-serif;
    font-size: 35px;
    line-height: 40px;
    color: var(--title-black);
  }
  .subtitle strong { font-weight: 700; }
  .author {
    position: absolute;
    left: 76px; top: 1138px;
    margin: 0;
    font-family: "Montserrat", sans-serif;
    font-weight: 700;
    font-size: 50px;
    line-height: 60px;
    letter-spacing: 5px;
    color: var(--author-green);
  }
  .badge {
    position: absolute;
    left: 536px; top: 855px;
    width: 274px; height: 274px;
  }
  .badge-text {
    position: absolute;
    left: 536px; top: 925px;
    width: 274px;
    text-align: center;
    font-family: "Montserrat", sans-serif;
    font-weight: 700;
    font-size: 35px;
    line-height: 38px;
    color: var(--text-white);
  }
</style>
</head>
<body>
  <main class="cover">
    <div class="produce produce-top-left" role="img" aria-label="Photo of fresh lettuce leaves and cucumbers in the top left corner"></div>
    <div class="produce produce-top-centre" role="img" aria-label="Photo of cherry tomatoes on the vine along the top edge"></div>
    <div class="produce produce-top-right" role="img" aria-label="Photo of lettuce and red cabbage in the top right corner"></div>
    <div class="produce produce-basket" role="img" aria-label="Photo of a wicker basket filled with peppers, red cabbage, tomatoes and onions"></div>
    <div class="produce produce-fruit" role="img" aria-label="Photo of oranges, grapes, apples, kiwis, grapefruit and cabbage"></div>

    <h1 class="title">
      <span class="title-top"><span class="title-rule"></span>ORCHARD AND<span class="title-rule"></span></span>
      <span class="title-main">GREENS 202</span>
    </h1>

    <div class="series-band">GARDEN PARTNER SOWING</div>

    <p class="subtitle">Partner Handbook On<br>Raising Crops<br>Through <strong>Basic,<br>Natural &amp; Lasting<br>Plot Methods</strong></p>

    <p class="author">AMBER HOLLOW</p>

    <svg class="badge" viewBox="0 0 274 274" aria-hidden="true">
      <circle cx="137" cy="137" r="135" fill="var(--title-orange)"/>
      <circle cx="137" cy="137" r="123" fill="none" stroke="var(--text-white)" stroke-width="5"/>
    </svg>
    <div class="badge-text">PERFECT<br>FOR<br>BEGINNERS</div>
  </main>
</body>
</html>
```